Tovimar Community Development Planning New web site

Design a new web site. I have a budget of $1,500.00.
Attached on PowerPoint is a complete site plan. Home page and linked pages.
10 - 12 pages. All copy and photos will be supplied. (300dpi)
I have shown them the concept which they like.
No data bases required. Home page with animations dissolving.
They former web site has been taken down. They have been in business 30 years in New Jersey
Colors teal blues and greens
There will be a new logo)being designed)
The text in home page copy will give you a detailed story what they are all about.

files have been approved for Tovimar, Inc.   Brenton is the designer

```html
<!DOCTYPE html>
<html lang="en">
<head>
<meta charset="utf-8">
<title>Tovimar, inc. — Community Development Planning</title>
<link href="https://fonts.googleapis.com/css2?family=Open+Sans:wght@400;600;700&family=Oswald:wght@500&display=swap" rel="stylesheet">
<style>
:root{
  --blue:#0a4fb4;
  --nav:#0d3f8f;
  --nav-dark:#082a62;
  --text:#555;
  --muted:#888;
  --red:#d0201a;
  --footer:#2b2b2b;
  --footer-base:#1b1b1b;
  --footer-text:#9a9a9a;
}
*{margin:0;padding:0;box-sizing:border-box}
html,body{width:847px;height:1200px;overflow:hidden}
body{position:relative;font-family:"Open Sans",Arial,sans-serif;color:var(--text);
  background:radial-gradient(ellipse at 50% 20%,#fff 0%,#f2f2f2 60%,#e6e6e6 100%)}
.abs{position:absolute}
.brand{left:71px;top:14px;font-size:22px;font-weight:600;color:var(--blue)}
.tagline{left:72px;top:43px;font-size:9px;color:#444}
.social{top:14px;width:17px;height:17px;background:#e4e4e4;border:1px solid #c9c9c9}
.search-field{left:572px;top:42px;width:144px;height:22px;background:#fff;border:1px solid #ddd;font-size:8px;color:#aaa;padding:5px 5px}
.search-btn{left:718px;top:42px;width:59px;height:22px;background:var(--blue);color:#fff;font-size:9.5px;font-weight:600;text-align:center;line-height:22px}
.nav{left:73px;top:76px;width:705px;height:39px;display:flex;background:linear-gradient(#1552a8,var(--nav))}
.nav a{display:block;height:39px;line-height:39px;text-align:center;color:#fff;font-size:9px;font-weight:600;text-decoration:none;border-right:1px solid #0a356f}
.nav a.active{background:var(--nav-dark)}
.hero{left:73px;top:115px;width:705px;height:293px;background:linear-gradient(160deg,#e9ecef 0%,#c9ccd0 45%,#9aa0a8 70%,#d8d8d6 100%)}
.hero-caption{left:73px;top:368px;width:705px;height:40px;background:rgba(40,40,40,.75)}
.hero-caption span{position:absolute;left:22px;top:11px;font-family:Oswald,sans-serif;font-size:12px;color:#fff}
.dot{top:386px;width:7px;height:7px;border-radius:50%;background:#fff}
h2{position:absolute;font-size:17px;font-weight:600;color:var(--blue)}
.about-img{left:72px;top:496px;width:84px;height:77px;background:radial-gradient(circle at 50% 35%,#6fc3f0,#0c5fa8 55%,#06203f)}
.about-text{font-size:8.4px;line-height:13.2px;color:#666;letter-spacing:-.1px}
.read-more{left:723px;top:456px;font-size:11px;color:var(--red)}
.date{left:541px;top:492px;font-size:9px;font-weight:700;color:#999}
.news-lead{left:541px;top:517px;width:230px;font-size:9.5px;font-weight:700;line-height:13px;color:#333}
.news-body{left:541px;top:558px;width:230px;font-size:9.5px;line-height:13px;color:#888}
.news-body a{color:var(--blue);text-decoration:none}
.service-img{top:692px;width:218px;height:122px}
.service-title{top:822px;width:218px;text-align:center;font-size:12px;font-weight:600;color:#444;line-height:16px}
.footer{left:0;top:926px;width:847px;height:237px;background:var(--footer)}
.footer-base{left:0;top:1163px;width:847px;height:37px;background:var(--footer-base);font-size:9px;color:#666;text-align:center;line-height:37px}
.f-head{top:960px;font-size:10px;color:#ddd}
.f-text{font-size:9px;line-height:12px;color:var(--footer-text)}
.f-link{font-size:9px;color:#ccc;font-weight:600;text-decoration:underline}
.f-circle{top:1082px;width:15px;height:15px;border-radius:50%;background:#555}
.f-input{left:602px;width:175px;height:28px;background:#fff;font-size:9px;color:#888;padding:8px 15px}
.f-submit{left:706px;top:1101px;width:71px;height:25px;background:var(--blue);color:#fff;font-size:9px;font-weight:600;text-align:center;line-height:25px}
</style>
</head>
<body>
<header>
  <div class="abs brand">Tovimar, inc.</div>
  <div class="abs tagline">Community Development Planning</div>
  <span class="abs social" style="left:688px"></span>
  <span class="abs social" style="left:709px"></span>
  <span class="abs social" style="left:731px"></span>
  <span class="abs social" style="left:752px"></span>
  <div class="abs search-field">Enter the keywords</div>
  <div class="abs search-btn">Search</div>
  <nav class="abs nav">
    <a class="active" style="width:83px">HOME</a>
    <a style="width:114px">OUR COMPANY</a>
    <a style="width:80px">SERVICES</a>
    <a style="width:174px">HOUSING REHAB APPLICATION</a>
    <a style="width:160px">AFFORDABLE APPLICATION</a>
    <a style="width:94px;border-right:0">CONTACT US</a>
  </nav>
</header>

<section>
  <div class="abs hero" role="img" aria-label="Planner working at a laptop over rolled plans and glasses"></div>
  <div class="abs hero-caption"><span>LOREM IPSUM DOLOR SIT AMMIT CONTANTRY POPILAR</span></div>
  <span class="abs dot" style="left:709px"></span>
  <span class="abs dot" style="left:720px"></span>
  <span class="abs dot" style="left:731px;background:#1a56b8"></span>
  <span class="abs dot" style="left:742px"></span>
  <span class="abs dot" style="left:752px"></span>
</section>

<section>
  <h2 style="left:73px;top:451px">About Us</h2>
  <div class="abs about-img" role="img" aria-label="Business team silhouettes before a globe"></div>
  <p class="abs about-text" style="left:169px;top:492px;width:340px">Tovimar, Inc. is a city planning firm that specializes in community development and housing rehabilitation program planning, design and implementation. We have over twenty years of experience in developing and administering income-based housing programs in accordance with National Office of Housing and Urban Renewal (NOHUR) and State Board on Affordable Homes (SBAH) rules and regulations. In addition,</p>
  <p class="abs about-text" style="left:69px;top:579px;width:452px">our firm is capable of providing the technical and administrative assistance our clients require for the implementation of their income-based housing programs. Tovimar's sister company, E. Walden Marsh Associates, is one of the most experienced urban planning firms in New Jersey, with over forty years as</p>

  <h2 style="left:541px;top:450px">News &amp; Events</h2>
  <div class="abs read-more">Read More</div>
  <div class="abs date">October 25, 2012, 9:32am</div>
  <p class="abs news-lead">Sed tellus nunc, ornare ac auctor non, tincidunt a orci.</p>
  <p class="abs news-body">Ut aliquam egestas eros, at molestie tellus scelerisque eget. <a>&gt;&gt;</a></p>
</section>

<section>
  <h2 style="left:0;width:826px;text-align:center;top:648px">Our Services</h2>
  <div class="abs service-img" style="left:71px;background:linear-gradient(135deg,#d9c9b0,#a98a66 50%,#e8e2d8)" role="img" aria-label="Family unpacking moving boxes"></div>
  <div class="abs service-img" style="left:314px;background:linear-gradient(135deg,#e6e6e2,#9bab8a 50%,#6f5a4c)" role="img" aria-label="Neighbors talking outside a home"></div>
  <div class="abs service-img" style="left:558px;background:linear-gradient(135deg,#f0f0f0,#7a7a7a 55%,#2a2a2a)" role="img" aria-label="Large dollar sign sculpture"></div>
  <div class="abs service-title" style="left:70px">Housing and Relocation</div>
  <div class="abs service-title" style="left:315px">Community and Economic<br>Development</div>
  <div class="abs service-title" style="left:559px">Grants and Funding Opportunities</div>
</section>

<footer>
  <div class="abs footer"></div>
  <div class="abs f-head" style="left:72px">Contact us</div>
  <p class="abs f-text" style="left:72px;top:988px">Lorem Ipsum<br>4120 Lindholt<br>Denmark</p>
  <p class="abs f-text" style="left:72px;top:1036px">+ 45 - So Call me Maybe</p>
  <p class="abs f-link" style="left:72px;top:1059px">Send us an e-mail</p>
  <span class="abs f-circle" style="left:73px"></span>
  <span class="abs f-circle" style="left:97px"></span>
  <span class="abs f-circle" style="left:120px;background:var(--blue)"></span>

  <div class="abs f-head" style="left:274px">Navigation</div>
  <p class="abs f-text" style="left:274px;top:988px">- Home<br>- Cases<br>- About<br>- Method<br>- Contact<br>- Blog</p>
  <div class="abs f-head" style="left:444px">Useful links</div>
  <p class="abs f-text" style="left:444px;top:988px">- Home<br>- Cases<br>- About<br>- Method<br>- Contact<br>- Blog</p>

  <div class="abs f-head" style="left:600px">Submit to our news letter</div>
  <p class="abs f-text" style="left:600px;top:984px;width:180px">Submit and get all the info about our work, new positions and new blog inputs.</p>
  <div class="abs f-input" style="top:1026px">Your Name</div>
  <div class="abs f-input" style="top:1061px">Your E-mail</div>
  <div class="abs f-submit">Submit</div>

  <div class="abs footer-base">All rights reserved - Tovimar, inc.</div>
</footer>
</body>
</html>
```